Modern and Simple Supplement Label Design

We are looking for a Professional Graphic Designer who can design eye-catching and unique supplement label. We are supplement company who are sourcing different supplement products. I would like the design to be simple and with few colorsThe final design should communicate strength and growthI attached some samples for inspiration

Target Market(s)

Supplement Market - Collagen Supplements

Industry/Entity Type

Supplement

Font styles to use
Serif
Sans Serif

Colors

Designer to choose colors to be used in the design.

Requirements
Must have
• Front (Please search on Brindleport Collagen to get inspiration how to put together the front text)
• Logo: Vellow Naturals
• Product Name: Omni Dermal Capsules
• Hydrolyzed type I II III V & X Collagen
• Dietary Supplements - 90 capsules
• Support Joints & bones
• Rejuvenate Skin
• Promotes Healthy Hair & Nails
• One right side supplement fact and left side precaution and instruction content. ( Please find the content of the right and left side of the bottle attached)
Nice to have
• Nice to have something that shows elements bring together to create something strong or beautiful. Our brand name is Vellow Naturals. Vellow is an assembly of beams or other elements that creates a rigid structure. This is to show our supplements help to provide the elements to have strong and healthy life

```html
<!DOCTYPE html>
<html lang="en">
<head>
<meta charset="utf-8">
<title>Vellow Naturals – Omni Dermal Capsules Label</title>
<link href="https://fonts.googleapis.com/css2?family=Archivo:wght@400;500;600;700;800;900&display=swap" rel="stylesheet">
<style>
  :root {
    --page: #ebebeb;
    --white: #ffffff;
    --navy: #1b2d86;
    --ink: #1a1f3a;
    --red: #dd1f2b;
    --sky: #2aa4df;
    --deep: #1c3d97;
    --silver-light: #f3f3f4;
    --silver-dark: #a9abb0;
    --rule: #ffffff;
  }
  * { box-sizing: border-box; margin: 0; padding: 0; }
  html, body { width: 1200px; height: 917px; overflow: hidden; }
  body {
    background: var(--page);
    font-family: "Archivo", Arial, sans-serif;
    color: var(--ink);
    position: relative;
  }
  .label {
    position: absolute;
    left: 50px; top: 265px;
    width: 1100px; height: 386px;
    background: var(--white);
    overflow: hidden;
  }
  .label__band { position: absolute; inset: 0; width: 100%; height: 100%; }
  .label__trim {
    position: absolute; left: 0; width: 100%; height: 7px;
    background: linear-gradient(180deg, var(--silver-light), var(--silver-dark), var(--silver-light));
  }
  .label__trim--top { top: 0; }
  .label__trim--bottom { bottom: 0; }

  /* left panel */
  .info-box {
    position: absolute; left: 22px; width: 302px;
    border: 1.5px solid var(--navy);
    background: var(--white);
    padding: 4px 7px;
    font-size: 10.5px; line-height: 1.3;
  }
  .info-box__title { font-weight: 700; color: var(--navy); text-transform: uppercase; font-size: 10.5px; }
  .info-box--use { top: 14px; height: 76px; }
  .info-box--caution { top: 95px; height: 85px; }
  .info-box--warning { top: 185px; height: 56px; text-align: center; font-weight: 800; color: var(--navy); text-transform: uppercase; }
  .info-box--notice { top: 247px; height: 54px; }
  .lot-note { position: absolute; left: 22px; top: 354px; font-size: 10.5px; color: var(--white); }

  /* center panel */
  .front {
    position: absolute; left: 402px; top: 18px; width: 340px;
    display: flex; flex-direction: column; align-items: center;
  }
  .brand { display: flex; align-items: center; gap: 6px; font-size: 16px; font-weight: 600; color: var(--navy); white-space: nowrap; }
  .brand__dot { width: 10px; height: 10px; border-radius: 50%; background: var(--red); }
  .product-name {
    margin-top: 12px; width: 291px; height: 60px;
    border: 3px solid #b9bbc0;
    background: var(--white);
    text-align: center; padding-top: 4px;
  }
  .product-name__main { display: block; font-size: 29px; font-weight: 900; color: var(--red); line-height: 1.05; letter-spacing: 0.5px; white-space: nowrap; }
  .product-name__sub { display: block; font-size: 15px; font-weight: 800; color: var(--navy); letter-spacing: 5px; }
  .type-bar {
    margin-top: 30px; padding: 0 14px; height: 24px;
    background: linear-gradient(180deg, var(--silver-light), #c7c8cc);
    font-size: 15px; font-weight: 800; color: var(--navy); letter-spacing: 1.5px;
    text-align: center; line-height: 24px; white-space: nowrap;
  }
  .type-bar--red {
    margin-top: 2px; padding: 0 10px; height: 24px;
    background: var(--red); color: var(--white); letter-spacing: 0.3px; font-size: 14px;
  }
  .benefits { list-style: none; margin-top: 12px; text-align: center; }
  .benefits li {
    font-size: 14px; font-weight: 500; color: var(--white); text-transform: uppercase;
    padding: 3px 0; white-space: nowrap;
  }
  .benefits li + li::before {
    content: ""; display: block; width: 80px; height: 1px; background: var(--rule); margin: 0 auto 5px;
  }
  .count { margin-top: 10px; display: flex; align-items: center; gap: 6px; font-weight: 800; color: var(--white); font-size: 16px; letter-spacing: 1px; }
  .count__badge {
    width: 28px; height: 22px; border-radius: 11px; background: var(--white); color: var(--navy);
    font-size: 14px; text-align: center; line-height: 22px; letter-spacing: 0;
  }
  .count-note { margin-top: 4px; font-size: 10px; font-weight: 600; color: var(--white); letter-spacing: 1px; text-transform: uppercase; }

  /* right panel */
  .facts {
    position: absolute; left: 848px; top: 14px; width: 228px; height: 222px;
    border: 1.5px solid var(--ink); background: var(--white);
    padding: 3px 7px; font-size: 10px; line-height: 1.3;
  }
  .facts__title { font-size: 19px; font-weight: 800; line-height: 1.1; }
  .facts__rule { border: 0; border-top: 4px solid var(--ink); margin: 3px 0; }
  .facts__rule--thin { border-top-width: 1px; }
  .facts__row { display: flex; justify-content: space-between; }
  .facts__head { justify-content: flex-end; gap: 22px; }
  .facts__foot { font-size: 9.5px; }
  .ingredients {
    position: absolute; left: 848px; top: 243px; width: 230px;
    font-size: 10px; line-height: 1.3; color: var(--white);
  }
  .ingredients strong { font-weight: 700; }
</style>
</head>
<body>
  <section class="label" aria-label="Omni Dermal Capsules bottle label">
    <svg class="label__band" viewBox="0 0 1100 386" preserveAspectRatio="none" aria-hidden="true">
      <defs>
        <linearGradient id="bandFill" x1="0" y1="0" x2="0" y2="1">
          <stop offset="0" stop-color="#2aa4df"/>
          <stop offset="0.45" stop-color="#1f7fcc"/>
          <stop offset="1" stop-color="#1c3d97"/>
        </linearGradient>
        <linearGradient id="bandFade" x1="0" y1="0" x2="0" y2="1">
          <stop offset="0" stop-color="#2aa4df" stop-opacity="0"/>
          <stop offset="1" stop-color="#2aa4df" stop-opacity="0.55"/>
        </linearGradient>
      </defs>
      <rect x="0" y="130" width="1100" height="50" fill="url(#bandFade)"/>
      <path d="M0 172 C 300 168, 700 178, 1100 168 L1100 386 L0 386 Z" fill="url(#bandFill)"/>
    </svg>
    <div class="label__trim label__trim--top"></div>
    <div class="label__trim label__trim--bottom"></div>

    <div class="info-box info-box--use">
      <p class="info-box__title">Suggested use:</p>
      <p>Take three (3) capsules one or more times a day or as directed by your care professional. For best results take on an empty stomach with 8 oz. glass of water.</p>
    </div>
    <div class="info-box info-box--caution">
      <p class="info-box__title">Caution</p>
      <p>Do not exceed recommended dose. Pregnant or nursing mothers, children under age of 18 and individuals with a known medical condition should consult a physician before using this or any dietary supplement.</p>
    </div>
    <div class="info-box info-box--warning">
      <p>Keep out of reach of children.<br>Do not use if safety seal is damaged or missing. Store in a cool, dry place</p>
    </div>
    <div class="info-box info-box--notice">
      <p>*These statements have not been evaluated by the Food and Drug Administration. This product is not intended to diagnose, treat, cure or prevent diseases.</p>
    </div>
    <p class="lot-note">Lot# and expiration date printed on bottom of bottle</p>

    <div class="front">
      <div class="brand"><span class="brand__dot"></span>Vellow Naturals</div>
      <h1 class="product-name">
        <span class="product-name__main">OMNI DERMAL</span>
        <span class="product-name__sub">CAPSULES</span>
      </h1>
      <div class="type-bar">HYDROLYZED TYPE</div>
      <div class="type-bar type-bar--red">I, II, III, V &amp; X COLLAGEN</div>
      <ul class="benefits">
        <li>Support Joints &amp; Bones</li>
        <li>Rejuvenate Skin</li>
        <li>Promotes Healthy Hair &amp; Nails</li>
      </ul>
      <div class="count"><span class="count__badge">90</span>CAPSULES</div>
      <p class="count-note">Dietary Supplements</p>
    </div>

    <div class="facts">
      <p class="facts__title">Supplement Facts</p>
      <p>Serving size: 3 Capsules</p>
      <p>Servings Per Container: 30</p>
      <hr class="facts__rule">
      <div class="facts__row facts__head"><span>Amount Per Serving</span><span>%DV</span></div>
      <hr class="facts__rule facts__rule--thin">
      <div class="facts__row"><span>Premium Collagen<br>Protein Complex</span><span>1500 mg</span><span>**</span></div>
      <hr class="facts__rule facts__rule--thin">
      <p>Bovine Collagen Peptides, Hydrolyzed, Pure Hydrolyzed Marine Collagen Peptides, Eggshell Membrane Collagen Peptides, Avian Sternum Collagen Peptides</p>
      <hr class="facts__rule">
      <p class="facts__foot">** Daily Value not established (DV)</p>
    </div>
    <div class="ingredients">
      <p><strong>Inactive Ingredient:</strong> Gelatin Capsules</p>
      <p><strong>Contains:</strong> Egg, Fish</p>
      <p><strong>Contains no added:</strong> Milk, Tree Nuts, Wheat, Peanuts, Soy, Shellfish</p>
    </div>
  </section>
</body>
</html>
```